Tolbek cards

I want a simple business card that pops.
Logo on one side.
On side two i want.
"Are you thinking about a new building on your property, or renovating an existing structure? Contact".....
Owners Name: Dale Whitacre
Owners Phone number: 610-555-0187
Address:4076 Copper Ridge RD, Halden, PA 16944
Committed to Quality, Service, and Integrity

```html
<!DOCTYPE html>
<html lang="en">
<head>
<meta charset="utf-8">
<title>Tolbek Builders LLC – Business Cards</title>
<link href="https://fonts.googleapis.com/css2?family=Arimo:ital,wght@0,400;0,700;1,400&display=swap" rel="stylesheet">
<style>
  :root {
    --backdrop: #5a5a5a;
    --card-white: #ffffff;
    --brown-dark: #4e3420;
    --brown-text: #5a3e2b;
    --brown-mid: #7a5c44;
    --brown-glow: #9c856d;
    --brown-edge: #563823;
    --grey-text: #555555;
    --rule: #cfcfcf;
    --cream: #efe6d6;
  }
  * { box-sizing: border-box; margin: 0; padding: 0; }
  html, body { width: 1200px; height: 1200px; overflow: hidden; }
  body {
    background: var(--backdrop);
    font-family: "Arimo", Arial, sans-serif;
    position: relative;
  }
  .card {
    position: absolute;
    width: 690px;
    height: 394px;
    overflow: hidden;
  }
  .card--front { left: 266px; top: 158px; background: var(--card-white); }
  .card--back {
    left: 260px;
    top: 651px;
    background: radial-gradient(ellipse 55% 60% at 45% 50%, var(--brown-glow) 0%, var(--brown-mid) 55%, var(--brown-edge) 100%);
  }

  .pitch {
    position: absolute;
    left: 51px; top: 30px;
    font-style: italic;
    font-size: 18.5px;
    line-height: 23.6px;
    color: var(--brown-text);
    white-space: nowrap;
  }
  .brand {
    position: absolute;
    display: flex;
    align-items: center;
    gap: 10px;
    font-weight: 700;
    color: var(--brown-dark);
    white-space: nowrap;
  }
  .brand__mark { display: block; background: currentColor; }
  .card--front .brand { right: 44px; top: 66px; font-size: 21px; }
  .card--front .brand__mark { width: 24px; height: 24px; }

  .owner-name {
    position: absolute;
    left: 49px; top: 260px;
    font-size: 27px;
    line-height: 30px;
    font-weight: 700;
    letter-spacing: 0.5px;
    color: var(--brown-dark);
  }
  .rule {
    position: absolute;
    left: 49px; top: 300px;
    width: 596px; height: 1px;
    background: var(--rule);
  }
  .phone {
    position: absolute;
    left: 46px; top: 310px;
    display: flex; align-items: center; gap: 9px;
    font-size: 16px;
    color: var(--grey-text);
  }
  .phone svg { width: 14px; height: 14px; fill: var(--brown-dark); }
  .address {
    position: absolute;
    right: 41px; top: 313px;
    font-size: 16px;
    color: var(--grey-text);
  }

  .footer-band { position: absolute; left: 0; bottom: 0; width: 690px; height: 32px; }
  .tagline {
    position: absolute;
    left: 358px; bottom: 9px;
    font-size: 14px;
    color: var(--card-white);
  }

  .card--back .brand {
    left: 50%; top: 46%;
    transform: translate(-50%, -50%);
    font-size: 36px;
    color: var(--cream);
    gap: 16px;
  }
  .card--back .brand__mark { width: 38px; height: 38px; }
</style>
</head>
<body>

  <section class="card card--front" aria-label="Business card, contact side">
    <p class="pitch">Are you thinking about a<br>new building on your<br>property, or renovating an<br>existing structure?</p>

    <div class="brand">
      <span class="brand__mark" aria-hidden="true"></span>
      <span class="brand__name">TOLBEK BUILDERS LLC</span>
    </div>

    <h1 class="owner-name">DALE WHITACRE</h1>
    <div class="rule"></div>

    <div class="phone">
      <svg viewBox="0 0 24 24" aria-hidden="true"><path d="M6.6 10.8c1.4 2.8 3.8 5.1 6.6 6.6l2.2-2.2c.3-.3.7-.4 1-.2 1.1.4 2.3.6 3.6.6.6 0 1 .4 1 1V20c0 .6-.4 1-1 1C10.6 21 3 13.4 3 4c0-.6.4-1 1-1h3.5c.6 0 1 .4 1 1 0 1.3.2 2.5.6 3.6.1.3 0 .7-.2 1l-2.3 2.2z"/></svg>
      <span>610-555-0187</span>
    </div>
    <p class="address">4076 Copper Ridge RD, Halden, PA 16944</p>

    <svg class="footer-band" viewBox="0 0 690 32" aria-hidden="true">
      <defs>
        <linearGradient id="stripGrad" x1="0" x2="1" y1="0" y2="0">
          <stop offset="0" stop-color="#7a5c44"/>
          <stop offset="0.5" stop-color="#a08a72"/>
          <stop offset="1" stop-color="#6d5039"/>
        </linearGradient>
      </defs>
      <rect x="0" y="16" width="310" height="16" fill="url(#stripGrad)"/>
      <polygon points="333,0 690,0 690,32 304,32" fill="#4e3420"/>
      <line x1="333" y1="0" x2="304" y2="32" stroke="#ffffff" stroke-width="3"/>
    </svg>
    <p class="tagline">Committed to Quality, Service, and Integrity</p>
  </section>

  <section class="card card--back" aria-label="Business card, logo side">
    <div class="brand">
      <span class="brand__mark" aria-hidden="true"></span>
      <span class="brand__name">TOLBEK BUILDERS LLC</span>
    </div>
  </section>

</body>
</html>
```